Quorva - corporate Business Card

We need a good look and innovative business card for a new start up company based in Los Angeles called "Quorva". We are in a payment business, including payment card, app, and ewallet. We are expert in online payment and Card not present (CNP) transaction.
We need an innovative, modern business card.

Our logo font is Aero Matics

Target Market(s)

Startup - Bank - Online Payment - Card Manufacturing

Industry/Entity Type

Startup

Contact Information for Business Card

phone: 555 014 7396 - Address: 4172 Marlowe blvd, Cylver City, CA 90299

Requirements
Must have
• Message: innovative, professional, expert, high tech, trust, online payment expert, security
Nice to have
• no comment
Should not have
• no Comment

```html
<!DOCTYPE html>
<html lang="en">
<head>
<meta charset="utf-8">
<title>Quorva – Business Card</title>
<link href="https://fonts.googleapis.com/css2?family=Ubuntu:wght@400;500;700&display=swap" rel="stylesheet">
<style>
  :root {
    --brand-red: #b81f2e;
    --frost: #eeeae9;
    --frost-edge: #e2dcdb;
    --backdrop: #f6f4f3;
    --ink-light: #ffffff;
    --pattern-red: #c4424f;
  }
  * { box-sizing: border-box; margin: 0; padding: 0; }
  html, body {
    width: 1200px; height: 900px; overflow: hidden;
    background: var(--backdrop);
    font-family: "Ubuntu", sans-serif;
  }
  .canvas { position: relative; width: 1200px; height: 900px; }

  .card {
    position: absolute;
    display: flex;
    border-radius: 40px;
    overflow: hidden;
    box-shadow: 0 6px 22px rgba(0,0,0,0.12);
    background: var(--frost);
    border: 1px solid var(--frost-edge);
  }
  .card--front { left: 238px; top: 62px; width: 554px; height: 342px; }
  .card--back  { left: 459px; top: 517px; width: 559px; height: 343px; }

  .card__face { position: relative; height: 100%; }
  .card--front .card__face--frost { width: 298px; }
  .card--back  .card__face--frost { width: 301px; }
  .card__face--red { flex: 1; background: var(--brand-red); color: var(--ink-light); }

  .brand {
    position: absolute; display: flex; align-items: center; gap: 10px;
    color: var(--brand-red);
  }
  .brand__dot {
    width: 74px; height: 74px; border-radius: 50%; background: var(--brand-red); flex: none;
  }
  .brand__name { font-weight: 500; font-size: 46px; letter-spacing: 1px; line-height: 1; }
  .card--front .brand { left: 28px; top: 132px; }

  .brand--ghost {
    left: 28px; top: 133px; opacity: 0.28;
    transform: scaleX(-1);
  }

  .contact { position: absolute; left: 18px; top: 70px; }
  .contact__name { font-weight: 700; font-size: 26px; line-height: 1; }
  .contact__role { font-weight: 500; font-size: 17px; margin-top: 7px; }
  .contact__list { list-style: none; margin-top: 27px; }
  .contact__item { display: flex; align-items: center; gap: 9px; font-size: 16px; height: 26px; }
  .contact__icon { width: 21px; height: 21px; flex: none; }
  .contact__address { font-size: 15px; line-height: 21px; margin-top: 20px; }

  .pattern-field { position: absolute; inset: 0; background: var(--pattern-red); opacity: 0.9; }
</style>
</head>
<body>
<main class="canvas">

  <section class="card card--front" aria-label="Business card front">
    <div class="card__face card__face--frost">
      <div class="brand">
        <span class="brand__dot"></span>
        <span class="brand__name">quorva</span>
      </div>
    </div>
    <div class="card__face card__face--red">
      <div class="contact">
        <h1 class="contact__name">Dana Whitford</h1>
        <p class="contact__role">Director</p>
        <ul class="contact__list">
          <li class="contact__item">
            <svg class="contact__icon" viewBox="0 0 24 24" aria-hidden="true">
              <circle cx="12" cy="12" r="11" fill="#fff"/>
              <rect x="8.5" y="5" width="7" height="14" rx="1.5" fill="none" stroke="#b81f2e" stroke-width="1.6"/>
              <circle cx="12" cy="16.6" r="0.9" fill="#b81f2e"/>
            </svg>
            <span>555 014 7396</span>
          </li>
          <li class="contact__item">
            <svg class="contact__icon" viewBox="0 0 24 24" aria-hidden="true">
              <circle cx="12" cy="12" r="11" fill="#fff"/>
              <circle cx="12" cy="12" r="6" fill="none" stroke="#b81f2e" stroke-width="1.6"/>
              <path d="M6 12h12M12 6c-2.5 3-2.5 9 0 12M12 6c2.5 3 2.5 9 0 12" fill="none" stroke="#b81f2e" stroke-width="1.2"/>
            </svg>
            <span>www.quorva.com</span>
          </li>
        </ul>
        <p class="contact__address">4172 Marlowe blvd,<br>Brenmoor City, CA 90299</p>
      </div>
    </div>
  </section>

  <section class="card card--back" aria-label="Business card back">
    <div class="card__face card__face--frost">
      <div class="brand brand--ghost">
        <span class="brand__dot"></span>
        <span class="brand__name">quorva</span>
      </div>
    </div>
    <div class="card__face card__face--red">
      <div class="pattern-field" role="img" aria-label="Repeating brand-mark pattern in soft red on the card back"></div>
    </div>
  </section>

</main>
</body>
</html>
```